Catalogue Design Project

We need a catalog design for a new private university called Redwell Institute Bayshore (see website www.rwi-bs.org). The catalog should be about 30 pages maximum and will include items such as General Information, Academic schedule, department descriptions, program descriptions, course descriptions, school policies, student services, admissions, San diego Lifestyle, etc.
I will provide the text but I need a professional design with regard to page layouts. I have provided some examples.
Ok, i posted the catalog content, just missing course descriptions.
Target Market(s)
Young Professionals, Foreign Students
Industry/Entity Type
University
Look and feel
Each slider illustrates characteristics of the customer's brand and the style your logo design should communicate.

```html
<!DOCTYPE html>
<html lang="en">
<head>
<meta charset="utf-8">
<title>Starting Your Own Business Certificate — Redwell Institute Bayshore</title>
<link rel="stylesheet" href="https://fonts.googleapis.com/css2?family=Carlito:ital,wght@0,400;0,700;1,400&display=swap">
<style>
  :root {
    --ink: #111111;
    --brand-blue: #2f6ea8;
    --rule-blue: #5f88b4;
    --accent-blue: #2f6597;
    --accent-grey: #a6a6a6;
    --footer-grey: #9a9a9a;
    --paper: #ffffff;
    --photo-light: #f3ece0;
    --photo-mid: #d8c4a0;
    --photo-deep: #b99a6c;
  }
  * { margin: 0; padding: 0; box-sizing: border-box; }
  html, body { width: 927px; height: 1200px; overflow: hidden; background: var(--paper); }
  body { font-family: "Carlito", Calibri, Arial, sans-serif; color: var(--ink); }

  .page { position: relative; width: 927px; height: 1200px; overflow: hidden; }

  .header-ornament {
    position: absolute; left: 61px; top: 36px; width: 163px; height: 34px;
    border-radius: 4px;
    background: linear-gradient(90deg, var(--accent-blue) 0%, var(--accent-grey) 25%, var(--accent-grey) 75%, var(--accent-blue) 100%);
    opacity: 0.55;
  }

  .header-photo {
    position: absolute; left: 560px; top: 0; width: 367px; height: 103px;
    background: linear-gradient(90deg, rgba(255,255,255,1) 0%, var(--photo-light) 30%, var(--photo-mid) 65%, var(--photo-deep) 100%);
  }
  .header-rule {
    position: absolute; left: 0; top: 102px; width: 927px; height: 2px; background: var(--rule-blue);
  }
  .section-banner {
    position: absolute; left: 538px; top: 105px; width: 389px; height: 35px;
    background: var(--brand-blue); color: #fff;
    font-size: 32px; line-height: 35px; padding-left: 38px; white-space: nowrap;
  }

  .content { position: absolute; left: 80px; top: 185px; width: 802px; font-size: 20px; line-height: 27.3px; }
  .content h1 { text-align: center; font-size: 27.5px; font-weight: 700; line-height: 34px; }
  .content p { text-align: justify; }
  .content p + p { margin-top: 27.3px; }
  .meta strong { font-weight: 700; }
  .block { margin-top: 27.3px; }
  .block-label { text-decoration: underline; }

  .footer-rule { position: absolute; left: 0; top: 1157px; width: 927px; height: 1px; background: var(--rule-blue); }
  .footer-mark { position: absolute; left: 704px; top: 1170px; font-size: 13.5px; color: var(--footer-grey); letter-spacing: 0.3px; white-space: nowrap; }
</style>
</head>
<body>
<div class="page">
  <div class="header-ornament" role="img" aria-label="Decorative cluster of blue and grey dots"></div>

  <div class="header-photo" role="img" aria-label="Photograph of an open old book with warm, faded pages"></div>
  <div class="header-rule"></div>
  <div class="section-banner">CERTIFICATE PROGRAMS</div>

  <main class="content">
    <h1>Starting Your Own Business Certificate</h1>
    <p>Staring your own business should be the ultimate goal for any entrepreneur or anyone really wanting to get ahead in life.&nbsp; This certificate prepares future business owners for today's market and what's required to get a successful product out there.&nbsp; The certificate covers many of the steps needed to get ready, including the initial decision-making process related to deciding the type of business: franchise, independent, service, manufacturing, retail, online, consumer, or business-to-business.&nbsp; Also mentioned are start-up requirements such as selecting the type of corporation to form, applying to receive articles of incorporation, opening a business bank account, purchasing a business owner insurance policy, worker's compensation, applying for a business license, creating employment agreements, writing company policies and many others.</p>
    <p>Subsequently, the course heavily focuses on researching ideas and ensuring that everything is well investigated before making the product or service available.&nbsp; Putting a product out on the market too quickly can squander precious resources and potentially be penalized by being positioned incorrectly in the marketplace.&nbsp; It's far better to be methodical and diligently research a prospect not just with respect to the product itself, but also to competition, existing substitutes, viability, and demand.&nbsp; The best method for covering all of ones bases is in the production of a business plan.&nbsp; It forces answers to all of the questions that must be asked in order to really find out if a product is going to be successful or not.&nbsp; Questions such as what the purpose of the business is, who the customers are, what problem does the product solve, what is the competitive advantage, what are the projections for future years, and what the best methods to pricing, positioning and marketing the product are.</p>
    <div class="meta"><strong>Hours:</strong> 6 hours per week</div>
    <div class="meta"><strong>Length:</strong> 8 weeks per course</div>

    <div class="block">
      <div class="block-label">Course:</div>
      <div>BUS 600 Starting Your Own Business</div>
    </div>

    <div class="block">
      <div class="block-label">Learning Outcome:</div>
      <p>Open a legitimate company with a clear idea for achieving profit, create a logo and website, secure a location, conduct in-depth research, and market a product.</p>
    </div>
  </main>

  <div class="footer-rule"></div>
  <div class="footer-mark">10::: REDWELL INSTITUTE</div>
</div>
</body>
</html>
```